Residential Remodeling Contractor needs updated business card

I need a new design for my business card.
Name of the company is Ridgefell Construction. I need a card that commands presence, strength, integrity. I have been in business for 28 years. I am a Residential Remodeling Contractor that covers all aspects of a residential remodel and build.

```html
<!DOCTYPE html>
<html lang="en">
<head>
<meta charset="utf-8">
<title>Ridgefell Construction — Business Card</title>
<link href="https://fonts.googleapis.com/css2?family=Montserrat:wght@400;500;600;700&display=swap" rel="stylesheet">
<style>
  :root {
    --backdrop: #b3b3b3;
    --card-navy: #223d7a;
    --ink-white: #ffffff;
    --ink-soft: rgba(255,255,255,0.85);
    --rule: rgba(255,255,255,0.8);
  }
  * { margin: 0; padding: 0; box-sizing: border-box; }
  html, body {
    width: 1200px; height: 900px; overflow: hidden;
    background: var(--backdrop);
    font-family: "Montserrat", Arial, sans-serif;
    color: var(--ink-white);
  }
  .sheet {
    width: 1200px; height: 900px;
    display: flex; flex-direction: column; align-items: center; justify-content: center;
    gap: 20px;
  }
  .card {
    position: relative;
    width: 700px; height: 400px;
    background: var(--card-navy);
    box-shadow: 0 6px 18px rgba(0,0,0,0.25);
    overflow: hidden;
  }
  .wordmark {
    font-weight: 600;
    letter-spacing: 0.06em;
    text-transform: uppercase;
    line-height: 1.15;
    color: var(--ink-white);
  }

  /* Front */
  .card-front .wordmark {
    position: absolute; left: 290px; top: 70px;
    font-size: 30px;
  }
  .card-front .wordmark span { display: block; }
  .card-front .wordmark .wordmark-sub { font-size: 22px; letter-spacing: 0.12em; }
  .divider {
    position: absolute; left: 40px; right: 40px; top: 228px;
    height: 1px; background: var(--rule);
  }
  .person {
    position: absolute; left: 40px; top: 160px;
  }
  .person-name { font-weight: 700; font-size: 26px; letter-spacing: 0.01em; }
  .person-role { font-weight: 400; font-size: 14px; color: var(--ink-soft); margin-top: 4px; }
  .contact-list {
    position: absolute; left: 40px; top: 252px;
    list-style: none;
    display: flex; flex-direction: column; gap: 12px;
  }
  .contact-item {
    display: flex; align-items: center; gap: 12px;
    font-size: 14px; font-weight: 400; color: var(--ink-soft);
  }
  .contact-item svg { width: 16px; height: 16px; flex: none; }
  .address {
    position: absolute; right: 40px; top: 262px;
    padding-left: 12px;
    border-left: 2px solid var(--rule);
    font-size: 14px; line-height: 1.45; color: var(--ink-soft);
  }

  /* Back */
  .card-back { display: flex; align-items: center; justify-content: center; }
  .card-back .wordmark { font-size: 40px; text-align: left; }
  .card-back .wordmark span { display: block; }
  .card-back .wordmark .wordmark-sub { font-size: 30px; letter-spacing: 0.12em; }
</style>
</head>
<body>
<main class="sheet">

  <section class="card card-front" aria-label="Card front">
    <div class="wordmark">
      <span>Ridgefell</span>
      <span class="wordmark-sub">Construction</span>
    </div>

    <div class="person">
      <p class="person-name">Daniel Harlow</p>
      <p class="person-role">Owner</p>
    </div>

    <div class="divider"></div>

    <ul class="contact-list">
      <li class="contact-item">
        <svg viewBox="0 0 16 16" aria-hidden="true"><path fill="#fff" d="M3.6 1.5l2.2 2.6-1.3 1.6c.9 2 2.4 3.6 4.4 4.6l1.6-1.3 2.6 2.2-1.2 2.3C6.7 13 2.9 9.3 1.4 3.1z"/></svg>
        888.555.0142
      </li>
      <li class="contact-item">
        <svg viewBox="0 0 16 16" aria-hidden="true"><rect x="1" y="3" width="14" height="10" rx="1" fill="#fff"/><path d="M1.5 3.5L8 9l6.5-5.5" stroke="#223d7a" stroke-width="1.3" fill="none"/></svg>
        info@ridgefellconstruction.com
      </li>
      <li class="contact-item">
        <svg viewBox="0 0 16 16" aria-hidden="true"><circle cx="8" cy="8" r="7" fill="#fff"/><path d="M1 8h14M8 1c-2.6 2.2-2.6 11.8 0 14M8 1c2.6 2.2 2.6 11.8 0 14" stroke="#223d7a" stroke-width="1" fill="none"/></svg>
        www.ridgefellconstruction.com
      </li>
    </ul>

    <address class="address" style="font-style: normal;">
      27 Quarry Ridge Road<br>
      Clinton, MS 39056
    </address>
  </section>

  <section class="card card-back" aria-label="Card back">
    <div class="wordmark">
      <span>Ridgefell</span>
      <span class="wordmark-sub">Construction</span>
    </div>
  </section>

</main>
</body>
</html>
```